Lotstallmart.com Webpage Design

Design Brief for lotstallmart.com (Copy of Brief also in attached Word file)

Name of Website- lotstallmart.com (existing logo and look & feel of website to be changed)

Logo - Finalised. The logo files are attached with the brief as “logo.jpeg”. The “Blue- Grey” version of the logo is for use on lighter backgrounds and the “Orange-White” version of the logo is for use on darker backgrounds. (A full Black version of the logo is also attached). Both versions may be used in different parts of the website. All attached files are in .png format.
Status - The website in functional and is undergoing user trials. However, we want to improve the look & feel of the website so at it seems
a. cotemporary,
b. Easy to Navigate
c. professional and
d. Vibrant.

Please visit ‘lotstallmart.com’ to check out the website and its functionalities – please use it only as a reference for the features & functions to be provided, however the designer should use a ‘Free Hand’ in designing the composition of various parts of the webpage without getting too influenced by the existing design

Objective of the Website ‘lotstallmart.com –
a. It is a portal focussed on listing of ‘Retail’ specific real-estate properties by developers, owners and realty brokers. The properties shall listed under the following four categories-
i. Retail Malls
ii. Shopping Complexes
iii. High-street shops
iv. Retail Warehouses
*refer lotstallmart.com for better clarity

b. The abovementioned properties shall be listed either for ‘Sale’ or ‘rent\lease’ or both

c. Users shall visit the site in case they wish to acquire a retail \ shop space either on ‘sale’ or ‘rent’. These Users would be able to specify the ‘Search Criteria’ through the tool-bars provided on the website – the ‘Search Criteria’ shall comprise of ‘Type of space category’, ‘City’, ‘Locality’, transaction type ie ‘Rent \ Sale’ and ‘Area Range’

d. The main revenue model for the website shall be listing fee ( or advertising charges ) payable by those listing their properties on the website.

Three Main Pages of Website (lotstallmart.com) that need to be designed -
a. Main Home Page (visit the web link - http://lotstallmart.com/ ) - The main home page has the “Search Toolbar” for specifying of Search Criteria by the User. It shall also have the following features & functions-
i. Main Advertising Banner
ii. Featured Projects
iii. New Launches
iv. Toolbar with buttons – ‘Advertise with Us’, ‘Listings Alert’, ‘Mart Wizards’, ‘Advertiser Login’

b. Property Listings Page (visit the web link - http://lotstallmart.com/gurgaon-in-india ) - The List of property options that match the Criteria specified by the ‘User’ get displayed on this page.

c. Property Detail Page - When the ‘User’ clicks on the “More….” Button on the ‘Property Listings Page’ (given in point b. above) the web page with the details of the property opens. (For Example – visit the web link - http://lotstallmart.com/vorne-Shopping-Complex-vorne-quadrion-gurgaon-636 )

Note:- Please refer to attached ‘Shopping’ related images the designer may use them on the website to provide a look & feel of retail if required – either separately or rotate in a single window

Target Market(s)

Retailers & Investors looking for retail space, Real Estate Brokers, Developers

Industry/Entity Type

Advertising

Number of Pages Required

3 page

Requirements
Must have
• Refer to existing site lotstallmart.com -- all the existing functionalities are a must have.
Nice to have
• The Designer may use the retail related images on the website if required for making it more vibrant. Refer attached images Shopping(1-6).jpg

```html
<!DOCTYPE html>
<html lang="en">
<head>
<meta charset="utf-8">
<title>Lotstallmart.com – Retail Space Portal</title>
<link rel="stylesheet" href="https://fonts.googleapis.com/css2?family=Open+Sans:wght@400;600;700&family=Roboto:wght@400;500;700&display=swap">
<style>
:root{
  --blue:#2f86c8;
  --blue-dark:#1e6aa6;
  --blue-strip:#2a7dbd;
  --link:#1a8be0;
  --text:#3d3d3d;
  --muted:#6b6b6b;
  --topbar:#3b3b3b;
  --hero:#1d3550;
  --panel:#f1efe9;
  --grey-bg:#eceef5;
  --pale-blue:#dbeaf9;
  --red:#c0282d;
  --footer:#1f1f1f;
  --line:#c9c9c9;
}
*{box-sizing:border-box;margin:0;padding:0}
html,body{width:1200px;height:2782px;overflow:hidden}
body{font-family:"Open Sans",Arial,sans-serif;color:var(--text);background:#fff;position:relative}
.abs{position:absolute}

/* top bar */
.topbar{left:0;top:0;width:1200px;height:26px;background:var(--topbar);border-top:3px solid var(--blue)}
.topbar .cities{left:98px;top:4px;color:#fff;font-size:11px;font-weight:600}
.topbar .social{right:98px;top:6px;display:flex;gap:6px}
.topbar .social span{width:10px;height:10px;background:#fff;display:block}

/* header */
.header{left:0;top:26px;width:1200px;height:114px;background:#fff}
.brand{left:98px;top:34px;display:flex;align-items:center;gap:8px}
.brand .dot{width:30px;height:30px;border-radius:50%;background:var(--blue)}
.brand .name{font-size:26px;font-weight:700;color:#2b5f8f}
.nav{left:436px;top:54px;display:flex;gap:0;font-size:13px}
.nav a{color:var(--text);text-decoration:none;position:absolute;white-space:nowrap}
.nav a.active{color:var(--link)}
.nav a.active::after{content:"";position:absolute;left:0;right:0;bottom:-6px;height:2px;background:var(--link)}
.login{left:974px;top:44px;width:128px;height:34px;background:linear-gradient(#3b95d8,#1f6fb0);color:#fff;font-size:13px;font-weight:600;text-align:center;line-height:34px;border-radius:2px}

/* hero */
.hero{left:0;top:140px;width:1200px;height:537px;background:linear-gradient(#2a4866,#142435)}
.hero-photo{left:98px;top:42px;width:1002px;height:452px;border:2px solid #fff;background:linear-gradient(120deg,#c9a58b 0%,#8d6a5a 30%,#b8c3cc 55%,#7f909e 100%)}
.hero-nav{left:112px;top:460px;display:flex;gap:4px}
.hero-nav span{width:20px;height:20px;border-radius:50%;background:#444;display:block}
.search{left:788px;top:64px;width:288px;height:404px;background:var(--panel);box-shadow:0 0 8px rgba(0,0,0,.35);padding:20px 20px}
.search h3{font-size:11.5px;color:var(--link);font-weight:600;text-align:center;padding-bottom:14px;border-bottom:1px solid #ddd}
.checks{display:grid;grid-template-columns:1fr 1fr;gap:16px 6px;margin:16px 0 18px;font-size:11px;color:var(--muted)}
.checks label{display:flex;align-items:center;gap:6px}
.search .lbl{font-size:11px;color:var(--link);font-weight:600;margin:0 0 8px}
.search .field{height:30px;background:#fff;border:1px solid #ddd;font-size:11px;color:var(--muted);padding:7px 12px;margin-bottom:16px}
.search .go{width:84px;height:28px;margin:0 auto;background:linear-gradient(#3b95d8,#1f6fb0);color:#fff;font-size:12px;font-weight:600;text-align:center;line-height:28px}

/* category strip */
.cats{left:0;top:681px;width:1200px;height:69px;background:var(--blue-strip);border-top:2px solid #5aa6e0}
.cat{position:absolute;top:14px;color:#fff;text-align:center}
.cat b{display:block;font-size:14px;font-weight:700;letter-spacing:.2px}
.cat b::before{content:"";display:inline-block;width:10px;height:10px;border-radius:50%;background:#fff;margin-right:8px;vertical-align:0}
.cat small{font-size:11px}

/* sections */
.section-grey{left:0;top:750px;width:1200px;height:484px;background:var(--grey-bg)}
.section-white{left:0;top:1234px;width:1200px;height:476px;background:#fff}
.title{position:absolute;left:98px;width:1004px;text-align:center;font-family:"Roboto",sans-serif;font-size:22px;color:#2b2b2b}
.title::before,.title::after{content:"";position:absolute;top:50%;height:1px;background:#999;width:42px}
.rule{position:absolute;left:98px;width:1004px;height:1px;background:var(--line)}
.arrows{position:absolute;left:1070px;display:flex;gap:4px}
.arrows span{width:14px;height:14px;border-radius:50%;background:#aaa;display:block}
.cards{position:absolute;left:98px;display:flex;gap:22px}
.card{width:234px;height:323px;background:#fff;box-shadow:0 12px 14px -6px rgba(0,0,0,.35),0 0 3px rgba(0,0,0,.15);padding:10px;text-align:center}
.card .pic{height:146px}
.card .city{margin-top:12px;font-size:14px;font-weight:700;color:var(--link);display:inline-flex;align-items:center;gap:6px;padding-bottom:4px;border-bottom:2px solid var(--link)}
.card .name{font-size:12px;color:var(--text);line-height:20px;margin-top:8px;text-transform:uppercase}
.card .type{font-size:11px;color:var(--link);margin-top:2px}
.card .btn{width:166px;height:36px;margin:14px auto 0;background:linear-gradient(#3b95d8,#1f6fb0);color:#fff;font-size:13px;font-weight:700;line-height:36px;box-shadow:0 3px 0 #16558a}

/* widgets */
.widgets{left:0;top:1710px;width:1200px;height:360px;background:var(--pale-blue)}
.widget{position:absolute;top:47px;width:296px;height:265px;background:#fff;box-shadow:8px 10px 12px -4px rgba(0,0,0,.25)}
.widget h4{font-family:"Roboto",sans-serif;font-size:14px;font-weight:500;text-align:center;padding:14px 0;border-bottom:1px solid #ddd;color:#2b2b2b}
.widget .body{padding:16px 22px;font-size:11px;color:var(--muted);line-height:20px}
.widget .intro{display:flex;gap:12px}
.widget .ico{flex:0 0 26px;height:22px;background:#9a9a9a;margin-top:6px}
.widget .input{height:32px;border:1px solid #ddd;margin-top:14px;padding:6px 10px;font-size:11px;color:var(--muted)}
.widget .red{width:100px;height:32px;background:var(--red);color:#fff;font-size:12px;font-weight:600;text-align:center;line-height:32px;margin-top:16px}

/* news */
.news{left:0;top:2070px;width:1200px;height:412px;background:#fff}
.item{position:absolute;width:464px;height:100px}
.item .thumb{position:absolute;left:0;top:0;width:108px;height:97px;border:3px solid #fff;box-shadow:0 2px 5px rgba(0,0,0,.4)}
.item h5{position:absolute;left:134px;top:0;font-size:12px;font-weight:600;color:#2b2b2b}
.item .date{position:absolute;right:0;top:0;font-size:12px;color:var(--red);font-weight:600}
.item p{position:absolute;left:134px;top:26px;width:330px;font-size:11px;line-height:20px;color:var(--muted)}
.item .more{position:absolute;right:0;top:76px;font-size:11px;color:var(--red);font-weight:600}
.vline{position:absolute;left:599px;width:1px;height:74px;background:var(--line)}

/* footer */
.footer{left:0;top:2482px;width:1200px;height:300px;background:var(--footer);color:#fff}
.footer h6{position:absolute;top:32px;font-size:14px;font-weight:700;padding-bottom:12px;border-bottom:1px solid #777}
.footer ul{position:absolute;list-style:none;font-size:11px;line-height:20px}
.footer .about{position:absolute;left:441px;top:82px;width:322px;font-size:11px;line-height:20px;text-align:justify}
.footer .contact{position:absolute;left:893px;top:80px;font-size:11px;line-height:20px}
.footer .contact div{display:flex;gap:10px;margin-bottom:14px}
.footer .sq{display:flex;gap:6px;margin-left:0}
.footer .sq span{width:20px;height:20px;background:#fff;border-radius:3px;display:block}
.footer .bottom{position:absolute;left:98px;top:222px;width:1004px;border-top:1px solid #444}
.footer .copy{position:absolute;left:98px;top:252px;font-size:11px}
.footer .links{position:absolute;right:98px;top:252px;font-size:11px}
.footer .code{position:absolute;right:50px;top:252px;font-size:11px}
</style>
</head>
<body>

<div class="abs topbar">
  <div class="abs cities">Bangalore | Chennai | Greater Noida | Gurgaon | Hyderabad | Jaipur | Khanna | Kolkatta | Mumbai | Noida | Pune | Surat</div>
  <div class="abs social"><span></span><span></span><span></span><span></span></div>
</div>

<header class="abs header">
  <div class="abs brand"><span class="dot"></span><span class="name">lotstallmart</span></div>
  <nav class="abs nav">
    <a class="active" style="left:0">Home</a>
    <a style="left:94px">Advertise with us</a>
    <a style="left:254px">Mart Wizards</a>
    <a style="left:382px">Listing Aler</a>
  </nav>
  <div class="abs login">Advertiser Login</div>
</header>

<section class="abs hero">
  <div class="abs hero-photo" role="img" aria-label="Banner photo of a family shopping in a bright glass-roofed mall"></div>
  <div class="abs hero-nav"><span></span><span></span></div>
  <form class="abs search">
    <h3>Select Retail Format: Meaning of Retail Format</h3>
    <div class="checks">
      <label><svg width="10" height="10" viewBox="0 0 10 10"><path d="M1 5l3 3 5-7" stroke="#888" stroke-width="1.6" fill="none"/></svg>Retail Malls</label>
      <label><svg width="10" height="10" viewBox="0 0 10 10"><path d="M1 5l3 3 5-7" stroke="#888" stroke-width="1.6" fill="none"/></svg>Shopping Complex</label>
      <label><svg width="10" height="10" viewBox="0 0 10 10"><path d="M1 5l3 3 5-7" stroke="#888" stroke-width="1.6" fill="none"/></svg>High Street Shops</label>
      <label><svg width="10" height="10" viewBox="0 0 10 10"><path d="M1 5l3 3 5-7" stroke="#888" stroke-width="1.6" fill="none"/></svg>Retail Warehouses</label>
    </div>
    <div class="lbl">Sale Or Rent Or Both :</div>
    <div class="field">Both</div>
    <div class="lbl">Select City:</div>
    <div class="field">Select</div>
    <div class="lbl">Enter Keywords:</div>
    <div class="field">Select</div>
    <div class="go">SEARCH</div>
  </form>
</section>

<div class="abs cats">
  <div class="cat" style="left:98px;width:190px"><b>RETAIL MALLS</b><small>Centrally Air-Conditioned</small></div>
  <div class="cat" style="left:370px;width:200px"><b>SHOPPING COMPLEX</b><small>Non Air-Conditioned Building</small></div>
  <div class="cat" style="left:650px;width:190px"><b>HIGH STREET SHOPS</b><small>Road Facing Retail</small></div>
  <div class="cat" style="left:930px;width:190px"><b>RETAIL WAREHOUSES</b><small>Back-end Retail Storage</small></div>
</div>

<section class="abs section-grey">
  <div class="rule" style="top:59px"></div>
  <h2 class="title" style="top:44px"><span style="background:var(--grey-bg);padding:0 78px">Featured Retail Projects</span></h2>
  <div class="arrows" style="top:80px"><span></span><span></span></div>
  <div class="cards" style="top:114px">
    <article class="card"><div class="pic" role="img" aria-label="Photo of a green glass shopping building" style="background:linear-gradient(#cfe3ee,#8fa36a)"></div>
      <div class="city"><svg width="10" height="13" viewBox="0 0 10 13"><path d="M5 0a5 5 0 0 0-5 5c0 4 5 8 5 8s5-4 5-8a5 5 0 0 0-5-5z" fill="var(--red)"/><circle cx="5" cy="5" r="2" fill="#fff"/></svg>SURAT</div>
      <div class="name">Corven<br>Arcade</div><div class="type">Shopping Complex</div><div class="btn">VIEW THE LISTING</div></article>
    <article class="card"><div class="pic" role="img" aria-label="Photo of a mall facade with red signage" style="background:linear-gradient(#9fb3c9,#a03a3a)"></div>
      <div class="city"><svg width="10" height="13" viewBox="0 0 10 13"><path d="M5 0a5 5 0 0 0-5 5c0 4 5 8 5 8s5-4 5-8a5 5 0 0 0-5-5z" fill="var(--red)"/><circle cx="5" cy="5" r="2" fill="#fff"/></svg>CHENNAI</div>
      <div class="name">The Lumen Mall<br>Velacheri</div><div class="type">Shopping Complex</div><div class="btn">VIEW THE LISTING</div></article>
    <article class="card"><div class="pic" role="img" aria-label="Photo of a lit tower at night" style="background:linear-gradient(#1b2c5c,#6b5a2c)"></div>
      <div class="city"><svg width="10" height="13" viewBox="0 0 10 13"><path d="M5 0a5 5 0 0 0-5 5c0 4 5 8 5 8s5-4 5-8a5 5 0 0 0-5-5z" fill="var(--red)"/><circle cx="5" cy="5" r="2" fill="#fff"/></svg>GURGAON</div>
      <div class="name">Orbit Galleria 91<br>Golf Course Road</div><div class="type">Shopping Complex</div><div class="btn">VIEW THE LISTING</div></article>
    <article class="card"><div class="pic" role="img" aria-label="Photo of a glass commercial tower" style="background:linear-gradient(#2a4c7a,#8aa3bd)"></div>
      <div class="city"><svg width="10" height="13" viewBox="0 0 10 13"><path d="M5 0a5 5 0 0 0-5 5c0 4 5 8 5 8s5-4 5-8a5 5 0 0 0-5-5z" fill="var(--red)"/><circle cx="5" cy="5" r="2" fill="#fff"/></svg>NOIDA</div>
      <div class="name">Tide One<br>Sector-18</div><div class="type">Shopping Complex</div><div class="btn">VIEW THE LISTING</div></article>
  </div>
</section>

<section class="abs section-white">
  <div class="rule" style="top:51px"></div>
  <h2 class="title" style="top:36px"><span style="background:#fff;padding:0 78px">Featured New Launches</span></h2>
  <div class="arrows" style="top:72px"><span></span><span></span></div>
  <div class="cards" style="top:107px">
    <article class="card"><div class="pic" role="img" aria-label="Photo of a glass commercial tower" style="background:linear-gradient(#2a4c7a,#8aa3bd)"></div>
      <div class="city"><svg width="10" height="13" viewBox="0 0 10 13"><path d="M5 0a5 5 0 0 0-5 5c0 4 5 8 5 8s5-4 5-8a5 5 0 0 0-5-5z" fill="var(--red)"/><circle cx="5" cy="5" r="2" fill="#fff"/></svg>NOIDA</div>
      <div class="name">Tide One<br>Sector-18</div><div class="type">Shopping Complex</div><div class="btn">VIEW THE LISTING</div></article>
    <article class="card"><div class="pic" role="img" aria-label="Photo of a curved building at dusk" style="background:linear-gradient(#1a2a4a,#4a5a7a)"></div>
      <div class="city"><svg width="10" height="13" viewBox="0 0 10 13"><path d="M5 0a5 5 0 0 0-5 5c0 4 5 8 5 8s5-4 5-8a5 5 0 0 0-5-5z" fill="var(--red)"/><circle cx="5" cy="5" r="2" fill="#fff"/></svg>GURGAON</div>
      <div class="name">Kestra Trinity<br>Dwarka Expressway</div><div class="type">Shopping Complex</div><div class="btn">VIEW THE LISTING</div></article>
    <article class="card"><div class="pic" role="img" aria-label="Photo of a low retail block under blue sky" style="background:linear-gradient(#4a7ab8,#8a8070)"></div>
      <div class="city"><svg width="10" height="13" viewBox="0 0 10 13"><path d="M5 0a5 5 0 0 0-5 5c0 4 5 8 5 8s5-4 5-8a5 5 0 0 0-5-5z" fill="var(--red)"/><circle cx="5" cy="5" r="2" fill="#fff"/></svg>MOHALI</div>
      <div class="name">SCO in Sector 127<br>Sihon Majra</div><div class="type">Shopping Complex</div><div class="btn">VIEW THE LISTING</div></article>
    <article class="card"><div class="pic" role="img" aria-label="Photo of a lit mall front at night" style="background:linear-gradient(#101a30,#3a4a5a)"></div>
      <div class="city"><svg width="10" height="13" viewBox="0 0 10 13"><path d="M5 0a5 5 0 0 0-5 5c0 4 5 8 5 8s5-4 5-8a5 5 0 0 0-5-5z" fill="var(--red)"/><circle cx="5" cy="5" r="2" fill="#fff"/></svg>MYSORE</div>
      <div class="name">Glenway Mall<br>Hunsur Main Road</div><div class="type">Shopping Complex</div><div class="btn">VIEW THE LISTING</div></article>
  </div>
</section>

<section class="abs widgets">
  <div class="widget" style="left:98px">
    <h4>LISTING ALERT</h4>
    <div class="body">
      <div class="intro"><span class="ico"></span><span>Suscribe for Fortnightly Email update on New Listings @ Lotstallmart</span></div>
      <div class="input">Enter youe email</div>
      <div class="input">Shopping Complex</div>
      <div class="red">SUBSCRIBE</div>
    </div>
  </div>
  <div class="widget" style="left:451px">
    <h4>EDITOR'S CHOICE</h4>
    <div class="body">
      <div class="intro"><span class="ico"></span><span>A "Select" Listing of Retail Properties Handpicked by our Editors based on their own positive evaluation on parameters &amp; attributes such as Design Concept, Location, Developer, Success Potential. So Read On to Check Out for yourself ..........</span></div>
      <div class="red" style="margin-left:38px;margin-top:10px">VIEW MORE</div>
    </div>
  </div>
  <div class="widget" style="left:803px">
    <h4>MART WIZARDS</h4>
    <div class="body">
      <div class="intro"><span class="ico" style="border-radius:50% 50% 0 0"></span><span>Post your Retail Space requirement with us and our experts shall get back</span></div>
      <div class="input">Enter youe email</div>
      <div class="input">Add Describtion</div>
      <div class="red" style="width:76px">SEND</div>
    </div>
  </div>
</section>

<section class="abs news">
  <div class="rule" style="top:51px"></div>
  <h2 class="title" style="top:36px"><span style="background:#fff;padding:0 78px">Latest News</span></h2>
  <div class="item" style="left:98px;top:119px"><div class="thumb" role="img" aria-label="Photo of shoppers with bags" style="background:linear-gradient(#6a5a4a,#a07a5a)"></div><h5>LOREM IPSUM AVAILABLE</h5><span class="date">22/JAN/2025</span><p>Readable content of a page when looking at its layout. The point of using Lorem Ipsum is that it has a more-or-less normal tent here', making</p><span class="more">MORE +</span></div>
  <div class="vline" style="top:124px"></div>
  <div class="item" style="left:638px;top:119px"><div class="thumb" role="img" aria-label="Photo of a shopper holding bags" style="background:linear-gradient(#b8a080,#7a4a5a)"></div><h5>LOREM IPSUM AVAILABLE</h5><span class="date">25/JAN/2025</span><p>Readable content of a page when looking at its layout. The point of using Lorem Ipsum is that it has a more-or-less normal tent here', making</p><span class="more">MORE +</span></div>
  <div class="item" style="left:98px;top:267px"><div class="thumb" role="img" aria-label="Photo of colourful shopping bags" style="background:linear-gradient(#e0b030,#c04a3a)"></div><h5>LOREM IPSUM AVAILABLE</h5><span class="date">26/JAN/2025</span><p>Readable content of a page when looking at its layout. The point of using Lorem Ipsum is that it has a more-or-less normal tent here', making</p><span class="more">MORE +</span></div>
  <div class="vline" style="top:272px"></div>
  <div class="item" style="left:638px;top:267px"><div class="thumb" role="img" aria-label="Photo of a shopper with bright bags" style="background:linear-gradient(#d8c070,#c06a3a)"></div><h5>LOREM IPSUM AVAILABLE</h5><span class="date">25/JAN/2025</span><p>Readable content of a page when looking at its layout. The point of using Lorem Ipsum is that it has a more-or-less normal tent here', making</p><span class="more">MORE +</span></div>
</section>

<footer class="abs footer">
  <h6 style="left:98px;width:210px">ABOUT STALLPOINT RETAIL</h6>
  <ul style="left:98px;top:80px"><li>About Us</li><li>Privacy Policy</li><li>Terms of Use</li><li>Contact Us</li><li>Site Map</li></ul>
  <ul style="left:236px;top:80px"><li>Retail Malls</li><li>Shopping Complex</li><li>High Street Shops</li><li>Retail Warehouses</li></ul>
  <h6 style="left:441px;width:322px">WWW.LOTSTALLMART.COM</h6>
  <p class="about">Lotstallmart.com - About Us Lotstallmart.com is a ised Web based platform for Retail Space, featuring properties across India under various formats such as Retail Malls, Shopping Complexes, High-street Shops. Also featured are Retail houses which the logistic back-end for the retail business. Lotstallmart.com is useful to various category of users as follows- a. Devel More...</p>
  <h6 style="left:893px;width:209px">CONTACT US</h6>
  <div class="contact">
    <div><svg width="10" height="13" viewBox="0 0 10 13"><path d="M5 0a5 5 0 0 0-5 5c0 4 5 8 5 8s5-4 5-8a5 5 0 0 0-5-5z" fill="#fff"/></svg><span>Stallpoint Retail Unit 212, 2nd Floor,<br>Lorem Ipsum is simply,<br>Sector-x, Gurgaon - 122002</span></div>
    <div><svg width="12" height="12" viewBox="0 0 12 12"><path d="M2 1l3 0 1 3-2 1a7 7 0 0 0 3 3l1-2 3 1 0 3c-6 1-10-3-9-9z" fill="#fff"/></svg><span>000-000-0000</span></div>
    <div class="sq"><span></span><span></span><span></span><span></span></div>
  </div>
  <div class="bottom"></div>
  <div class="copy">Copyright © 2013 Stallpoint India.com. All rights reserved.</div>
  <div class="links" style="right:118px">Home | Advertise with us | Mart Wizards | Listing Aler</div>
  <div class="code">C11</div>
</footer>

</body>
</html>
```